Call Center In Need of Website Design

We are a call center that provides inbound and outbound calling & marketing services for eCommerce store. We would like to see a fun, creative, playful design that is simple.

Here are some sample design sites we like;
- https://www.velmoreline.com/
- https://pindrask.io/
- https://www.glimbertic.com/live-chat-software/
- https://www.zavrolin.com/

Here are some competitor sites;
- https://www.ostrevaglinks.com/
- https://www.helpkestrel.com/

I have attached website content for your use.

Target Market(s)

eCommerce

Coding

Coded - Design and coding required

Number of Pages Required

5+ page

Font styles to use
Sans Serif

Colors

Designer to choose colors to be used in the design.

Requirements
Must have
• Must have designs for the following 5 separate pages;
• 1. Home (landing)
• - This will be were the design style really needs to show.
• - Just needs to touch on key services
• - CTA
• 2. About Us
• - Basic page for about me paragraph
• 3. Services
• - List of services with icons
• - Click on service type to expand details or hover over service icon to view popup bubble with details about that service
• 4. Pricing
• - Option to bundle 1(one) digital service plan and 1(one) call center service plan
• - Bundling adds 10% monthly discount to over all price
• - Customer does NOT have to bundle
• - FAQ
• 5. Contact Us
• - Include a capture form (name, company name, email, phone, message)
• - Contact info
• - Business hours
• When customer purchases their desired plan, then they are taken to a page where they must schedule a call with an account rep.
Nice to have
• home page animations
Should not have
• All information on Home/Landing page.

```html
<!DOCTYPE html>
<html lang="en">
<head>
<meta charset="utf-8">
<title>Orbitalle — Pricing</title>
<link href="https://fonts.googleapis.com/css2?family=Anton&family=Raleway:wght@400;500;600;700&family=Lato:wght@400;700;900&display=swap" rel="stylesheet">
<style>
:root{
  --indigo:#373683;
  --ink:#2d2d6e;
  --teal:#6cc6ad;
  --teal-light:#7fd6bf;
  --teal-field:#8bdcc5;
  --violet:#8759b8;
  --olive:#87a93b;
  --text:#3a3a4a;
  --white:#ffffff;
  --mist:#f2f2f2;
}
*{box-sizing:border-box;margin:0;padding:0}
html,body{width:1200px;height:2791px;overflow:hidden;background:var(--white)}
body{position:relative;font-family:'Raleway',sans-serif;font-variant-numeric:lining-nums;color:var(--text)}
.abs{position:absolute}

/* hero */
.hero{left:0;top:0;width:1200px;height:390px;background:var(--indigo)}
.hero-green{left:0;top:390px;width:1200px;height:240px;background:var(--teal)}
.art-sky{left:0;top:340px;width:1200px;height:100px;background:linear-gradient(180deg,var(--indigo) 0%,var(--teal) 100%)}
.art-astronaut{left:790px;top:80px;width:410px;height:300px;background:linear-gradient(150deg,#4b4aa0 0%,#5f5fb0 60%,#3f3e8e 100%)}
.art-rocket{left:56px;top:100px;width:40px;height:270px;background:linear-gradient(180deg,#7fd6bf 0%,#4f8f98 100%)}
.art-flag{left:0;top:440px;width:200px;height:190px;background:linear-gradient(180deg,#7fd6bf 0%,#5fb39b 100%)}
.brand{left:164px;top:30px;display:flex;align-items:center;gap:18px;color:var(--white);font-weight:500;font-size:40px;letter-spacing:6px}
.brand-dot{width:44px;height:44px;border-radius:50%;background:var(--teal)}
.nav{left:563px;top:43px;display:flex;gap:38px;list-style:none}
.nav li{color:var(--white);font-family:'Lato',sans-serif;font-weight:700;font-size:11px;letter-spacing:.5px;text-transform:uppercase}
.nav li.active{border-bottom:2px solid var(--white);padding-bottom:3px}
.hero-title{left:162px;top:152px;color:var(--white);font-family:'Anton',sans-serif;font-size:56px;line-height:66px;font-weight:400;letter-spacing:1px}
.hero-sub{left:162px;top:300px;color:var(--white);font-size:17px;letter-spacing:4px}
.page-title{left:200px;top:500px;display:flex;align-items:center;gap:14px;color:var(--white);font-family:'Anton',sans-serif;font-weight:400;font-size:30px}
.page-title i{display:block;width:36px;height:3px;background:var(--white)}

/* pricing */
.plan{top:712px;width:205px;border-radius:14px;padding:0 9px;box-shadow:0 4px 8px rgba(0,0,0,.18)}
.plan-head{height:48px;display:flex;align-items:center;justify-content:center;color:var(--white);font-family:'Lato',sans-serif;font-weight:900;font-size:14px;text-transform:uppercase}
.plan-body{background:var(--white);border-radius:12px;padding:12px 10px 12px}
.price{display:flex;align-items:flex-start;justify-content:center;gap:4px;font-family:'Lato',sans-serif}
.price sup{font-size:11px;margin-top:6px}
.price b{font-size:32px;font-weight:400;line-height:32px}
.price span{font-size:10px;font-weight:900;margin-top:18px}
.trial{text-align:center;font-size:9px;font-weight:700;margin-top:2px}
.features{list-style:none;margin-top:12px}
.features li{font-size:10.5px;line-height:13px;margin-bottom:9.5px;padding-left:10px;position:relative;color:#333}
.features li::before{content:"";position:absolute;left:0;top:4px;width:5px;height:5px;border:1px solid #333;border-radius:50%}
.plan-cta{height:44px;display:flex;align-items:center;justify-content:center;color:var(--white);font-family:'Lato',sans-serif;font-weight:700;font-size:11px}
.plan.teal{left:164px;background:var(--teal)} .plan.teal .price{color:var(--teal)}
.plan.indigo{left:387px;background:var(--indigo)} .plan.indigo .price{color:var(--indigo)}
.plan.violet{left:610px;background:var(--violet)} .plan.violet .price{color:var(--violet)}
.plan.olive{left:833px;background:var(--olive)} .plan.olive .price{color:var(--olive)}

/* custom band */
.custom{left:0;top:1343px;width:1200px;height:192px;background:var(--indigo);border-top:4px solid #2a8f8a}
.custom p{position:absolute;left:161px;top:60px;width:880px;color:var(--white);font-size:16px;line-height:23px}

/* faq */
.faq-mark{left:585px;top:1643px;width:32px;height:8px;border-top:2px solid var(--ink);border-bottom:2px solid var(--ink)}
.faq-title{left:0;top:1651px;width:1200px;text-align:center;font-family:'Anton',sans-serif;font-size:30px;color:var(--ink);font-weight:400}
.faq-col{top:1717px;width:422px;display:flex;flex-direction:column;gap:11px}
.faq-col.left{left:164px}.faq-col.right{left:616px}
.q{height:36px;background:var(--mist);border-radius:18px;box-shadow:0 2px 4px rgba(0,0,0,.15);display:flex;align-items:center;justify-content:space-between;padding:0 16px;font-family:'Lato',sans-serif;font-weight:700;font-size:11px;color:#222}
.q b{font-size:20px;font-weight:700}
.q.open{height:auto;flex-direction:column;align-items:stretch;background:var(--teal);border-radius:14px;padding:12px 16px 14px;color:var(--white)}
.q.open .q-head{display:flex;justify-content:space-between;text-transform:uppercase;border-bottom:1px solid rgba(255,255,255,.6);padding-bottom:9px}
.q.open p{font-family:'Raleway',sans-serif;font-weight:500;font-size:10.5px;line-height:15px;margin-top:12px}

/* cta */
.cta-title{left:0;top:2093px;width:1200px;text-align:center;font-family:'Anton',sans-serif;font-weight:400;font-size:42px;line-height:54px;color:var(--ink);letter-spacing:1px}
.cta-btn{left:519px;top:2224px;width:160px;height:48px;border-radius:24px;background:var(--teal);color:var(--white);font-family:'Lato',sans-serif;font-weight:700;font-size:11px;display:flex;align-items:center;justify-content:center;text-transform:uppercase}
.art-launch{left:960px;top:2085px;width:150px;height:264px;background:linear-gradient(180deg,#ffffff 0%,#a9e3d3 35%,var(--teal) 100%)}

/* contact */
.contact-bg{left:0;top:2349px;width:1200px;height:348px;background:linear-gradient(90deg,#63b9a1 0%,#6cc6ad 40%,#62b79f 100%)}
.card{left:186px;top:2409px;width:275px;height:284px;background:var(--teal-light);padding:26px 24px;color:var(--white)}
.card h3{font-family:'Lato',sans-serif;font-size:15px;font-weight:700}
.card hr{border:0;height:2px;width:34px;background:var(--white);margin:10px 0 24px}
.line{display:flex;gap:12px;font-size:11px;line-height:16px;margin-bottom:14px}
.line svg{flex:none;margin-top:1px}
.form-title{left:488px;top:2408px;color:var(--white);font-weight:600;font-size:30px}
.field{width:253px;height:39px;background:var(--teal-field);color:var(--white);font-size:10px;display:flex;align-items:center;padding-left:12px}
.submit{left:488px;top:2595px;width:104px;height:38px;border:2px solid var(--white);border-radius:4px;color:var(--white);font-family:'Lato',sans-serif;font-weight:700;font-size:11px;display:flex;align-items:center;justify-content:center}

/* footer */
.copy{left:161px;top:2726px;font-size:10px;line-height:18px;color:#666}
.foot-nav{left:412px;top:2737px;display:flex;gap:26px;list-style:none;font-size:11px;color:#444}
.foot-nav li.active{color:var(--teal)}
.social{left:918px;top:2730px;display:flex;gap:6px}
.social span{width:24px;height:24px;border-radius:2px}
</style>
</head>
<body>

<header>
  <div class="abs hero"></div>
  <div class="abs hero-green"></div>
  <div class="abs art-sky" role="img" aria-label="Illustration of puffy clouds between a starry night sky and a green hill"></div>
  <div class="abs art-rocket" role="img" aria-label="Illustration of a small rocket with a vapour trail"></div>
  <div class="abs art-astronaut" role="img" aria-label="Illustration of an astronaut floating among stars"></div>
  <div class="abs art-flag" role="img" aria-label="Illustration of an astronaut planting a flag on a hill"></div>

  <div class="abs brand"><span class="brand-dot"></span>ORBITALLE</div>
  <ul class="abs nav">
    <li>Home</li><li>About Us</li><li>Services</li><li class="active">Pricing</li><li>Contact Us</li><li>Account</li>
  </ul>
  <h1 class="abs hero-title">Orbitalle Is An<br>Omnichannel</h1>
  <p class="abs hero-sub">Provider For Customer Care</p>
  <h2 class="abs page-title"><i></i>PRICING</h2>
</header>

<main>
  <section class="plan abs teal">
    <div class="plan-head">Digital Standard</div>
    <div class="plan-body">
      <div class="price"><sup>$</sup><b>199</b><span>PER MONTH</span></div>
      <ul class="features">
        <li>Unlimited Email Support</li>
        <li>Limited Live Chat Support</li>
        <li>Product Research (5 per month)</li>
        <li>Product Listing (5 per month)</li>
        <li>Price Monitoring (10 products per month)</li>
        <li>Product Photo &amp; Video Editing (5 photos &amp; 1, 10 second video)</li>
      </ul>
    </div>
    <div class="plan-cta">Sign Up Now</div>
  </section>

  <section class="plan abs indigo">
    <div class="plan-head">Call Center Standard</div>
    <div class="plan-body">
      <div class="price"><sup>$</sup><b>39</b><span>PER MONTH</span></div>
      <div class="trial">(7 Day Free Trail)</div>
      <ul class="features">
        <li>Pay Per Minute</li><li>$1.10 Per Minute</li><li>Live Personalized Receptionist</li>
        <li>Text &amp; Email Delivery</li><li>Includes Nationwide 800</li><li>Answering service</li>
        <li>Welcome Calls</li><li>Follow-Up Service</li><li>Customer Upselling</li>
        <li>Over-The-Phone Order Taking</li><li>Order Return Processing</li><li>Feedback/Survey Calls</li>
        <li>Message Delivering Service</li><li>ROI Diagnostics &amp; Reporting</li><li>Scalable Call Center Pricing</li>
        <li>Customizable For Any Industry</li><li>100% US-Based Agents</li>
      </ul>
    </div>
    <div class="plan-cta">Sign Up Now</div>
  </section>

  <section class="plan abs violet">
    <div class="plan-head">Digital Business</div>
    <div class="plan-body">
      <div class="price"><sup>$</sup><b>199</b><span>PER MONTH</span></div>
      <ul class="features">
        <li>Unlimited Email Support</li>
        <li>Unlimited Live Chat Support</li>
        <li>Product Research (20 per m.)</li>
        <li>Product Listing (20 per month)</li>
        <li>Price Monitoring (50 permonth)</li>
        <li>Product Photo &amp; Video Editing (20 photos &amp; 5, 10 sec video)</li>
      </ul>
    </div>
    <div class="plan-cta">Sign Up Now</div>
  </section>

  <section class="plan abs olive">
    <div class="plan-head">Call Center Business</div>
    <div class="plan-body">
      <div class="price"><sup>$</sup><b>249</b><span>PER MONTH</span></div>
      <div class="trial">(7 Day Free Trail)</div>
      <ul class="features">
        <li>225 Minutes</li><li>$1.05 Per Minute</li><li>Live Personalized Receptionist</li>
        <li>Text &amp; Email Delivery</li><li>Includes Nationwide 800 Number</li><li>Answering service</li>
        <li>Welcome Calls</li><li>Follow-Up Service</li><li>Customer Upselling</li>
        <li>Over-The-Phone Order Taking</li><li>Order Return Processing</li><li>Feedback/Survey Calls</li>
        <li>Message Delivering Service</li><li>ROI Diagnostics &amp; Reporting</li><li>Scalable Call Center Pricing</li>
        <li>Customizable For Any Industry</li><li>100% US-Based Agents</li>
      </ul>
    </div>
    <div class="plan-cta">Sign Up Now</div>
  </section>

  <section class="abs custom">
    <p>Have higher call volumes or require more minutes? This is when we like to customize a cost-effective answering service plan or call center solution to fit your budget and exceed your expectations.&nbsp; Contact us to tell us more about your requirements and get a custom quote.</p>
  </section>

  <div class="abs faq-mark"></div>
  <h2 class="abs faq-title">Frequently Asked Questions</h2>
  <div class="abs faq-col left">
    <div class="q open">
      <div class="q-head"><span>Is the free trial really free?</span><span>–</span></div>
      <p>The free trial only relates to the "call center" service packages! There is no hidden fine print or fees to get started. We don't even require any payment info, signatures, or deposits. If you don't like us or our service, just simply walk away.</p>
    </div>
    <div class="q">Do you offer custom script writing?<b>+</b></div>
    <div class="q">Why do you use time-based billing over standard billing?<b>+</b></div>
    <div class="q">How long does it take to get started?<b>+</b></div>
  </div>
  <div class="abs faq-col right">
    <div class="q">Do I have to sign a contract?<b>+</b></div>
    <div class="q">Do I have to purchase any hardware or equipment?<b>+</b></div>
    <div class="q">I'm not sure how many minutes I'll need?<b>+</b></div>
    <div class="q">Can I change my service plan?<b>+</b></div>
  </div>

  <div class="abs art-launch" role="img" aria-label="Illustration of a rocket launching from clouds"></div>
  <h2 class="abs cta-title">READY TO TAKE YOUR BUSINESS<br>TO THE NEXT LEVEL</h2>
  <div class="abs cta-btn">Get Started</div>
</main>

<footer>
  <div class="abs contact-bg" role="img" aria-label="Faint illustration of an astronaut on a planet surface"></div>
  <div class="abs card">
    <h3>Contact Details</h3>
    <hr>
    <div class="line">
      <svg width="12" height="12" viewBox="0 0 24 24"><path fill="#fff" d="M6.6 10.8a15 15 0 0 0 6.6 6.6l2.2-2.2a1 1 0 0 1 1-.25 11.4 11.4 0 0 0 3.6.6 1 1 0 0 1 1 1V20a1 1 0 0 1-1 1A17 17 0 0 1 3 4a1 1 0 0 1 1-1h3.5a1 1 0 0 1 1 1c0 1.25.2 2.45.6 3.6a1 1 0 0 1-.25 1z"/></svg>
      <span>Phone: (800) 555-0142</span>
    </div>
    <div class="line">
      <svg width="12" height="12" viewBox="0 0 24 24"><path fill="#fff" d="M2 5h20v14H2z"/><path fill="none" stroke="#7fd6bf" stroke-width="2" d="M2 5l10 8 10-8"/></svg>
      <span>info@orbitalle.inc</span>
    </div>
    <div class="line">
      <svg width="12" height="14" viewBox="0 0 24 28"><path fill="#fff" d="M12 0a9 9 0 0 0-9 9c0 7 9 19 9 19s9-12 9-19a9 9 0 0 0-9-9zm0 12.5A3.5 3.5 0 1 1 12 5.5a3.5 3.5 0 0 1 0 7z"/></svg>
      <span>Orbitalle, Inc.<br>418 Larkspur Ave. Marlow, CA 90210</span>
    </div>
  </div>

  <h2 class="abs form-title">Request For Call Back</h2>
  <div class="abs field" style="left:488px;top:2483px">Name</div>
  <div class="abs field" style="left:759px;top:2483px">Email</div>
  <div class="abs field" style="left:488px;top:2535px">Ph Num</div>
  <div class="abs field" style="left:759px;top:2535px">Enquiry About</div>
  <div class="abs submit">Submit Now</div>

  <p class="abs copy">Copyright © 2018<br>All rights reserved.</p>
  <ul class="abs foot-nav">
    <li class="active">Home</li><li>About Us</li><li>Service</li><li>Pricing</li><li>Contact Us</li><li>Account</li>
  </ul>
  <div class="abs social" aria-label="Social links">
    <span style="background:#2aa3e0"></span><span style="background:#3b5a9a"></span><span style="background:#4a7ca5"></span><span style="background:#d9483a"></span>
  </div>
</footer>

</body>
</html>
```